Web Design Project - brivolta

I'm building an agency for marketing solutions but also medical education and patients education for pharmaceutical companies, medical societies and patient advocacy groups. We want to be perceived as the most innovative in the market. We work through design thinking solutions for campaigns and services.
I love some websites based on Swiss style design like www.quorlinex.com
We are a small group of designers, physicians and creatives working together to deliver the best experiences in our market.
We decided to also use pixel bazaar expecting that we maybe found a great idea we didn't thought about yet.

I'm extending it for more 2 weeks

Reason: I need the best design you can. Only PSD. No code needed. Love Swiss style, like velmora 5 and quorlinex.com I'm extending the deadline until get something great. Willing to extend as much as needed.

Target Market(s)

Pharmaceutical companies, physicians, medical societies, patients advocacy groups

Industry/Entity Type

Pharmaceutical

Font styles to use
Other font styles liked:
• Helvetia family

Colors

Designer to choose colors to be used in the design.

Requirements
Must have
• Must be innovative like www.quorlinex.com
Nice to have
• Cool menus
Should not have
• Not to appear too much Comercial. We like to be a boutique in this market. Craftsmen working with less clients at time but delivering precious stones.

```html
<!DOCTYPE html>
<html lang="en">
<head>
<meta charset="utf-8">
<title>brivolta</title>
<link rel="stylesheet" href="https://fonts.googleapis.com/css2?family=Arimo:wght@400;700&family=Open+Sans:wght@300;400&display=swap">
<style>
:root{
  --cyan:#00c6f2;
  --orange:#ff6a00;
  --ink:#2b2b2b;
  --white:#ffffff;
  --grey:#b9b9b9;
  --rule:#d8d8d8;
  --hero-bg:#eef3f6;
}
*{box-sizing:border-box;margin:0;padding:0}
html,body{width:1039px;height:1200px;overflow:hidden}
body{background:var(--cyan);font-family:"Arimo",Helvetica,Arial,sans-serif;color:var(--ink);position:relative}
.site-header{position:absolute;left:0;top:0;width:1039px;height:78px;background:var(--white)}
.brand{position:absolute;left:78px;top:22px;font-size:33px;font-weight:400;color:var(--cyan);letter-spacing:-.3px}
.main-nav{position:absolute;left:0;top:0}
.nav-item{position:absolute;top:20px;width:40px;height:40px}
.nav-item svg{width:40px;height:40px}
.nav-item.is-active::after{content:"";position:absolute;left:-5px;top:51px;width:50px;height:4px;background:var(--orange)}
.nav-divider{position:absolute;top:16px;width:1px;height:50px;background:var(--rule)}
.page{position:absolute;left:78px;top:119px;width:879px;height:1026px;background:var(--white)}
.hero{position:absolute;left:8px;top:9px;width:862px;height:335px;background:linear-gradient(100deg,#e3d6cc 0%,#c9dbe6 28%,#e9f1f5 52%,var(--hero-bg) 70%,#f5f6f7 100%)}
.hero-text{position:absolute;left:483px;top:52px;width:370px}
.hero-title{font-size:33px;font-weight:400;color:var(--cyan);white-space:nowrap}
.hero-title strong{font-weight:400;color:var(--orange);font-size:44px}
.hero-copy{margin-top:12px;font-family:"Open Sans",Arial,sans-serif;font-weight:300;font-size:17.5px;line-height:28.6px;letter-spacing:1.1px;color:#333}
.photo{position:absolute;background:linear-gradient(135deg,#c9c3bc,#8c99a8)}
.feature-photo{left:23px;top:371px;width:194px;height:153px;background:linear-gradient(135deg,#d7cfc3,#7f8c99 60%,#2d3a55)}
.feature-text{position:absolute;left:241px;top:374px;width:360px}
.feature-title{font-size:26px;font-weight:400;color:var(--orange)}
.feature-copy{margin-top:8px;font-family:"Open Sans",Arial,sans-serif;font-weight:300;font-size:19px;line-height:25px;letter-spacing:1.6px;color:#333}
.tile{position:absolute;overflow:hidden}
.tile-label{position:absolute;left:0;bottom:0;width:100%;height:38px;display:flex;align-items:center;justify-content:center;font-size:20px;font-weight:700;letter-spacing:.6px;background:rgba(246,246,246,.88);color:#111}
.tile-edu{left:623px;top:362px;width:242px;height:162px;border:3px solid #111;background:linear-gradient(120deg,#8aa07a,#c7b9ac 45%,#5f7fa8)}
.tile-edu .tile-label{background:rgba(20,20,20,.78);color:var(--white);font-weight:400;justify-content:flex-start;padding-left:16px;height:36px}
.tile-pharma{left:23px;top:568px;width:241px;height:189px;background:linear-gradient(135deg,#2f5fb8,#a9c4e2 45%,#e5eef6)}
.tile-marketing{left:325px;top:568px;width:241px;height:189px;background:linear-gradient(135deg,#cdb9a6,#eef0f2 45%,#3a4048)}
.tile-patients{left:621px;top:568px;width:241px;height:189px;background:linear-gradient(135deg,#8a7563,#dfe3e7 50%,#b8c6d6)}
.societies{position:absolute;left:23px;top:792px;width:241px;height:211px;background:var(--orange);color:var(--white);padding:18px 12px}
.societies-title{font-size:24px;font-weight:400;white-space:nowrap;letter-spacing:-.3px}
.societies-title strong{font-weight:400;font-size:29px;color:#111}
.societies-copy{margin-top:8px;padding-left:2px;font-family:"Open Sans",Arial,sans-serif;font-size:17px;line-height:24px;letter-spacing:.9px}
.contact{position:absolute;left:288px;top:792px;width:574px;height:214px;background:var(--grey);color:var(--white);padding:10px 14px}
.contact-name{font-size:44px;font-weight:400;line-height:50px}
.contact-list{list-style:none;margin-top:6px}
.contact-list li{display:flex;align-items:center;font-size:18px;height:36px}
.contact-list li.small{font-size:14px;height:30px}
.contact-list svg{width:12px;height:12px;margin-right:14px;flex:none}
.site-footer{position:absolute;left:0;top:1164px;width:1039px;text-align:center;color:var(--white);font-size:12px}
</style>
</head>
<body>
<header class="site-header">
  <div class="brand">brivolta</div>
  <nav class="main-nav" aria-label="Main">
    <a class="nav-item is-active" style="left:353px" aria-label="Home">
      <svg viewBox="0 0 40 40" fill="none" stroke="#222" stroke-width="2"><path d="M4 20 L20 5 L36 20"/><path d="M9 16 V35 H31 V16"/><path d="M17 35 V25 H23 V35"/></svg>
    </a>
    <span class="nav-divider" style="left:427px"></span>
    <a class="nav-item" style="left:456px" aria-label="Services">
      <svg viewBox="0 0 40 40" fill="none" stroke="#222" stroke-width="2"><rect x="5" y="11" width="30" height="24" rx="3"/><path d="M15 11 V6 H25 V11"/><path d="M20 17 V29 M14 23 H26" stroke-width="3"/></svg>
    </a>
    <span class="nav-divider" style="left:531px"></span>
    <a class="nav-item" style="left:560px" aria-label="Ideas">
      <svg viewBox="0 0 40 40" fill="none" stroke="#222" stroke-width="1.6"><circle cx="20" cy="17" r="8"/><path d="M17 25 V30 H23 V25"/><path d="M18 32 H22" stroke-width="3"/><path d="M20 3 V6 M8 8 L10 10 M32 8 L30 10 M4 17 H7 M33 17 H36"/></svg>
    </a>
    <span class="nav-divider" style="left:635px"></span>
    <a class="nav-item" style="left:658px" aria-label="Products">
      <svg viewBox="0 0 40 40" fill="none" stroke="#222" stroke-width="1.8"><rect x="14" y="3" width="12" height="5"/><rect x="12" y="10" width="16" height="27" rx="2"/><path d="M20 18 V29 M15 23.5 H25"/></svg>
    </a>
    <span class="nav-divider" style="left:896px"></span>
    <a class="nav-item" style="left:912px" aria-label="Contact">
      <svg viewBox="0 0 40 40" fill="none" stroke="#222" stroke-width="2"><rect x="5" y="10" width="30" height="21" rx="3"/><circle cx="14" cy="18" r="3"/><path d="M9 26 Q14 20 19 26"/><circle cx="27" cy="20" r="3"/></svg>
    </a>
  </nav>
</header>

<main class="page">
  <section class="hero">
    <div class="photo" role="img" aria-label="Photo of two doctors reviewing paperwork together" style="left:0;top:0;width:480px;height:335px;background:linear-gradient(100deg,#e0cfc2,#d3dde5 60%,rgba(233,241,245,0))"></div>
    <div class="hero-text">
      <h1 class="hero-title">welcome to <strong>brivolta</strong></h1>
      <p class="hero-copy">simply dummy text of the printing and typesetting industry. Lorem Ipsum has been the industry's standard dummy text ever since the 1500s, when an un-known printer took a galley.</p>
    </div>
  </section>

  <div class="photo feature-photo" role="img" aria-label="Photo of a business meeting with documents and a laptop"></div>
  <div class="feature-text">
    <h2 class="feature-title">Marketing Solutions</h2>
    <p class="feature-copy">simply dummy text of the printing and typesetting industry. Lorem Ipsum has been the industry's stan-dard dummy text ever since the 1500s.</p>
  </div>

  <div class="tile tile-edu" role="img" aria-label="Photo of students in a lecture">
    <span class="tile-label">Medical Education</span>
  </div>
  <div class="tile tile-pharma" role="img" aria-label="Photo of pills and capsules">
    <span class="tile-label">Pharmaceutical</span>
  </div>
  <div class="tile tile-marketing" role="img" aria-label="Photo of a person using a laptop">
    <span class="tile-label">Marketing Solutions</span>
  </div>
  <div class="tile tile-patients" role="img" aria-label="Photo of a person typing on a laptop">
    <span class="tile-label">Patients Education</span>
  </div>

  <section class="societies">
    <h3 class="societies-title">medical <strong>societies</strong></h3>
    <p class="societies-copy">Lorem Ipsum has been the industry's standard dummy text ever since the 1500s, when an un-known printer</p>
  </section>

  <section class="contact">
    <div class="contact-name">brivolta</div>
    <ul class="contact-list">
      <li><svg viewBox="0 0 12 12"><path d="M2 1 L4.5 1 L5.5 3.5 L4 4.8 Q5.2 7 7.2 8 L8.5 6.5 L11 7.5 L11 10 Q6 11 1 3 Z" fill="#222"/></svg>+44 1632 960418</li>
      <li><svg viewBox="0 0 12 12"><rect x="1" y="3" width="10" height="7" fill="#222"/><path d="M1 3 L6 7 L11 3" stroke="#b9b9b9" fill="none"/></svg>info@brivolta.com</li>
      <li><svg viewBox="0 0 12 12" fill="#222"><rect x="5" y="1" width="2" height="10"/><rect x="1" y="2" width="4" height="3"/><rect x="7" y="5" width="4" height="3"/></svg>27 Larkmoor Row, Fenwick, FN4 2KD, USA</li>
      <li class="small"><svg viewBox="0 0 12 12"><circle cx="6" cy="6" r="5" fill="none" stroke="#222" stroke-width="1.4"/><path d="M8 4.5 A2.2 2.2 0 1 0 8 7.5" fill="none" stroke="#222" stroke-width="1.3"/></svg>2014 brivolta. All Rights Reserved | Privacy Policy</li>
    </ul>
  </section>
</main>

<footer class="site-footer">© &nbsp;2014 brivolta. All Rights Reserved | Privacy Policy</footer>
</body>
</html>
```